Brightarc Orthodontics appointment card design

I need appointment cards/ business cards made. Front will be Logo, name, title, email, phone number and location (5263 Walnut Hollow Pkwy, Ste 412, Concord, NC 28027) . the back should have an appointment card (name, time, date) and also 3 addresses listed with a check box so we can check to which location they are going.
Dale Fenwick Orthodontics
- 6735 Orchard Street, Ste 514, Harrisburg, NC 28075
- 3647 Ridgeway Drive NE, Ste 810, Concord, NC 28025
- 2917 Thornbury Corporate Drive, Ste 605, Charlotte, NC 28277
Business card can be horizontal or vertical in Design.
I need to be able to edit it to update and add new employees

Requirements
Must have
• Front:
• - Logo
• - Name & Title (able to be edited)
• - phone (704-555-0186) & Email (need to be able to edit)
• - Address: 5263 Walnut Hollow Pkwy, Ste 412
• Concord, NC 28027
• Back:
• Appointment Card design:
• - Name, time, Date
• - 3 locations w/ a check box so the patient knows where to go:
• Dale Fenwick Orthodontics
• - 6735 Orchard Street, Ste 514, Harrisburg, NC 28075
• - 3647 Ridgeway Drive NE, Ste 810, Concord, NC 28025
• - 2917 Thornbury Corporate Drive, Ste 605, Charlotte, NC 28277

```html
<!DOCTYPE html>
<html lang="en">
<head>
<meta charset="utf-8">
<title>Brightarc Orthodontics – Appointment & Business Card</title>
<link href="https://fonts.googleapis.com/css2?family=Roboto:wght@300;400;500;700&display=swap" rel="stylesheet">
<style>
  :root {
    --backdrop: #3a3b3e;
    --brand-blue: #1883c2;
    --brand-blue-dark: #0f6fae;
    --ink: #4a4a4a;
    --rule: #555;
    --paper: #ffffff;
  }
  * { box-sizing: border-box; margin: 0; padding: 0; }
  html, body {
    width: 1200px; height: 1000px; overflow: hidden;
    background: var(--backdrop);
    font-family: "Roboto", Arial, sans-serif;
  }
  .card {
    position: absolute; left: 250px;
    width: 700px; height: 400px;
    border-radius: 26px; overflow: hidden;
    box-shadow: 0 10px 30px rgba(0,0,0,.35);
  }

  /* Appointment side */
  .appointment { top: 50px; background: var(--paper); color: var(--ink); }
  .appointment .top-band { position: absolute; top: 0; left: 0; right: 0; height: 16px; background: var(--brand-blue); }
  .appointment .heading {
    position: absolute; left: 40px; top: 48px;
    font-size: 22px; font-weight: 700; color: var(--brand-blue-dark);
  }
  .appointment .wordmark {
    position: absolute; right: 40px; top: 62px;
    display: flex; align-items: center; gap: 10px;
    font-size: 38px; font-weight: 700; color: var(--brand-blue-dark);
  }
  .wordmark .dot { width: 14px; height: 14px; border-radius: 50%; background: currentColor; }
  .field { position: absolute; display: flex; align-items: flex-end; font-size: 14px; }
  .field .label { margin-right: 8px; }
  .field .line { flex: 1; border-bottom: 1.5px solid var(--rule); height: 1px; margin-bottom: 3px; }
  .field-name { left: 40px; top: 128px; width: 380px; }
  .field-date { left: 40px; top: 168px; width: 380px; }
  .field-time { left: 40px; top: 208px; width: 620px; }
  .field-time .line:first-child { margin-right: 10px; }
  .meridiem { position: absolute; right: 40px; top: 240px; display: flex; gap: 18px; font-size: 15px; }
  .checkbox {
    display: inline-block; width: 15px; height: 15px;
    border: 2px solid var(--brand-blue-dark); vertical-align: -2px; margin-right: 5px;
  }
  .practice {
    position: absolute; left: 0; right: 0; top: 266px; text-align: center;
    font-size: 17px;
  }
  .practice strong { font-size: 21px; font-weight: 700; color: var(--brand-blue-dark); }
  .location { position: absolute; font-size: 13px; line-height: 1.35; text-align: center; }
  .location .checkbox { display: block; margin: 0 auto 6px; }
  .loc-harrisburg { left: 30px; top: 262px; }
  .loc-concord { left: 250px; top: 305px; }
  .loc-charlotte { right: 28px; top: 330px; }

  /* Business side */
  .business { top: 530px; background: var(--brand-blue); color: #fff; }
  .business .wordmark {
    position: absolute; left: 50px; top: 150px;
    display: flex; align-items: center; gap: 14px;
    font-size: 62px; font-weight: 700;
  }
  .business .divider { position: absolute; left: 385px; top: 95px; width: 1.5px; height: 210px; background: rgba(255,255,255,.85); }
  .contact { position: absolute; left: 410px; top: 110px; font-size: 16px; line-height: 1.3; }
  .contact .person { font-size: 22px; font-weight: 700; letter-spacing: .3px; }
  .contact .title { font-size: 16px; font-weight: 300; margin-bottom: 16px; }
  .contact .address { margin-bottom: 10px; }
  .contact .row { display: flex; align-items: center; gap: 8px; }
  .contact svg { width: 14px; height: 14px; flex: none; }
</style>
</head>
<body>

<section class="card appointment">
  <div class="top-band"></div>
  <h2 class="heading">Next Appointment</h2>
  <div class="wordmark"><span class="dot"></span>Brightarc</div>

  <div class="field field-name"><span class="label">Name</span><span class="line"></span></div>
  <div class="field field-date"><span class="label">Date</span><span class="line"></span></div>
  <div class="field field-time"><span class="line"></span><span class="label">Time</span><span class="line"></span></div>

  <div class="meridiem">
    <span><span class="checkbox"></span>AM</span>
    <span><span class="checkbox"></span>PM</span>
  </div>

  <p class="practice"><strong>Dale Fenwick</strong> Orthodontics</p>

  <div class="location loc-harrisburg"><span class="checkbox"></span>6735 Orchard Street, Ste 514,<br>Harrisburg, NC 28075</div>
  <div class="location loc-concord"><span class="checkbox"></span>3647 Ridgeway Drive NE, Ste 810,<br>Concord, NC 28025</div>
  <div class="location loc-charlotte"><span class="checkbox"></span>2917 Thornbury Corporate Drive,<br>Ste 605, Charlotte, NC 28277</div>
</section>

<section class="card business">
  <div class="wordmark">Brightarc</div>
  <div class="divider"></div>
  <div class="contact">
    <p class="person">DALE FENWICK</p>
    <p class="title">Orthodontics</p>
    <p class="address">5263 Walnut Hollow Pkwy,<br>Ste 412 - Concord, NC 28027</p>
    <p class="row">
      <svg viewBox="0 0 24 24" aria-hidden="true"><path fill="#fff" d="M6.6 10.8a15.1 15.1 0 0 0 6.6 6.6l2.2-2.2a1 1 0 0 1 1-.25 11.4 11.4 0 0 0 3.6.57 1 1 0 0 1 1 1V20a1 1 0 0 1-1 1A17 17 0 0 1 3 4a1 1 0 0 1 1-1h3.5a1 1 0 0 1 1 1c0 1.25.2 2.45.57 3.57a1 1 0 0 1-.25 1z"/></svg>
      704-555-0186
    </p>
    <p class="row">
      <svg viewBox="0 0 24 24" aria-hidden="true"><path fill="#fff" d="M3 5h18a1 1 0 0 1 1 1v12a1 1 0 0 1-1 1H3a1 1 0 0 1-1-1V6a1 1 0 0 1 1-1zm9 7.2L20 7H4z"/></svg>
      dalefenwick@brightarcmail.com
    </p>
  </div>
</section>

</body>
</html>
```